Kestrelbrook Student Accomodation needs a business card design

Hi Guys,

We are a Student Accommodation company in Australia. We already have a logo which I will submit.

I will require the design of the business cards from you.

I am after something that looks clean, modern and that people feel interested and actually want to contact us.

We would like to see designs that are innovative.

On the business cards I will require to have:

Employee Name
Position
Phone number
Email
Facebook page

I hope you can help me with this project guys as I have heard really good things from you.

```html
<!DOCTYPE html>
<html lang="en">
<head>
<meta charset="utf-8">
<title>Kestrelbrook Student Accomodation – Business Card</title>
<link rel="stylesheet" href="https://fonts.googleapis.com/css2?family=Exo+2:wght@400;600;700&display=swap">
<style>
  :root {
    --brand-green: #138f45;
    --brand-gold: #fbbd3a;
    --paper: #ffffff;
  }
  * { margin: 0; padding: 0; box-sizing: border-box; }
  html, body {
    width: 1200px;
    height: 726px;
    overflow: hidden;
    background: var(--paper);
  }
  .card {
    position: relative;
    width: 1200px;
    height: 726px;
    background: var(--paper);
    font-family: "Exo 2", sans-serif;
  }
  .brand {
    position: absolute;
    left: 60px;
    top: 215px;
    display: flex;
    align-items: center;
    gap: 26px;
  }
  .brand-square {
    width: 150px;
    height: 150px;
    background: var(--brand-green);
    flex: none;
  }
  .brand-name {
    color: var(--brand-green);
    font-weight: 700;
    font-size: 40px;
    line-height: 1.1;
    text-transform: uppercase;
    letter-spacing: 1px;
  }
  .name-band {
    position: absolute;
    left: 600px;
    top: 240px;
    width: 600px;
    height: 143px;
    background: var(--brand-green);
    padding: 22px 0 0 23px;
  }
  .person-name {
    color: var(--brand-gold);
    font-weight: 700;
    font-size: 50px;
    line-height: 1;
    letter-spacing: 1.5px;
    text-transform: uppercase;
  }
  .person-role {
    color: var(--brand-gold);
    font-weight: 400;
    font-size: 27px;
    margin-top: 8px;
  }
  .contact-list {
    position: absolute;
    left: 623px;
    top: 426px;
    list-style: none;
    color: var(--brand-gold);
    font-size: 23.5px;
  }
  .contact-list li {
    display: flex;
    height: 30.5px;
    align-items: center;
  }
  .contact-label {
    width: 47px;
    font-weight: 700;
  }
  .contact-value { font-weight: 400; }
</style>
</head>
<body>
  <main class="card">
    <div class="brand">
      <div class="brand-square"></div>
      <div class="brand-name">Kestrelbrook<br>Student<br>Accomodation</div>
    </div>

    <section class="name-band">
      <h1 class="person-name">Darren Holloway</h1>
      <p class="person-role">National Sales Manager</p>
    </section>

    <ul class="contact-list">
      <li><span class="contact-label">P.</span><span class="contact-value">08 9000 4417</span></li>
      <li><span class="contact-label">E.</span><span class="contact-value">darren_holloway@kestrelbrook.com.au</span></li>
      <li><span class="contact-label">F.</span><span class="contact-value">xxxx@kestrelpage.xxx</span></li>
    </ul>
  </main>
</body>
</html>
```